Moxy Fen needs some awesome stationary

Do you have what it takes to get my brand? You either do or you don't, have a crack at a design and you my just win my business.

I don't want to waste your or my time, so put your creative genius on either a business card or envelope.

I however need a package of stationary that follows the same brand. I will message you to complete the remaining should I like your first submission.

Here is what I need, have a go!

Basically I need the following for my small business based in melbourne.
- Letterhead (printer ready and MS Word)
- Business Card
- Compliments Slip
- Envelope
- Proposal Cover Page (MS Word only)
- Presentation Folder
- Marbled Fox Cards
- Student Name Tent
- Index Cards
- Vell-Ka

I am establishing the brand and it must be modern, professional but also relaxed; that is not formal and not corporate. It represents a company are leaders, but small enough to care and operate like a bunch of friends. We are bringing people and conversations back to business, and turfing out all the bureaucracy and crazy and wasteful procedures. Its about "lets talk and figure it out together and find even better ways".

Target Market(s)

Mainly companies that build software products, but Agile practices are used in many other industries (even graphic design projects)

Industry/Entity Type

Information Technology

Font styles to use
Sans Serif

Colors
3176b5
aaaaaa

Requirements
Must have
• I like curves and circles and not boxes or rectangles.
• I want a colour rich design with my brand colours, but it must be balanced.
• I want more modern than traditional, but simple modern
Should not have
• Not corporate
• Please don't waste my time if your not going to think about it.
• Don't mess with my primary logo
• Don't change my colours
• Don't overlay logo on image

```html
<!DOCTYPE html>
<html lang="en">
<head>
<meta charset="utf-8">
<title>Moxy Fen Stationery Suite</title>
<link href="https://fonts.googleapis.com/css2?family=Open+Sans:wght@400;600;700&family=Pinyon+Script&display=swap" rel="stylesheet">
<style>
  :root {
    --brand-blue: #3d5f9b;
    --brand-grey: #9aa1ab;
    --paper: #f7f7f7;
    --canvas: #ececec;
    --ink: #3d5f9b;
    --muted: #6f737a;
    --white: #ffffff;
  }
  * { box-sizing: border-box; margin: 0; padding: 0; }
  html, body { width: 1200px; height: 822px; overflow: hidden; }
  body {
    background: var(--canvas);
    font-family: "Open Sans", Arial, sans-serif;
    color: var(--muted);
    position: relative;
  }
  .piece {
    position: absolute;
    background: var(--paper);
    overflow: hidden;
    box-shadow: 0 1px 3px rgba(0,0,0,0.12);
  }
  .wave { position: absolute; left: 0; bottom: 0; width: 100%; display: block; }
  .wave .wave-grey { fill: var(--brand-grey); }
  .wave .wave-blue { fill: var(--brand-blue); }

  .brand {
    display: flex; align-items: center; gap: 5px;
    font-weight: 700; color: var(--brand-blue); white-space: nowrap;
  }
  .brand-dot { border-radius: 50%; background: var(--brand-blue); flex: none; }

  /* Letterhead */
  .letterhead { left: 349px; top: 111px; width: 313px; height: 446px; }
  .letterhead .brand { position: absolute; top: 36px; left: 0; width: 100%; justify-content: center; font-size: 12px; }
  .letterhead .brand-dot { width: 14px; height: 14px; }
  .letterhead .wave { height: 66px; }
  .letterhead-footer {
    position: absolute; bottom: 6px; left: 0; width: 100%;
    text-align: center; color: var(--white); font-size: 5.4px; line-height: 8px;
  }

  /* Presentation folder */
  .folder { left: 704px; top: 90px; width: 371px; height: 469px; background: var(--brand-blue); }
  .folder-spine { position: absolute; left: 0; top: 0; width: 21px; height: 100%; background: var(--brand-grey); }
  .folder-spine::after { content: ""; position: absolute; right: 0; top: 0; width: 2px; height: 100%; background: rgba(255,255,255,0.25); }
  .folder .brand {
    position: absolute; top: 190px; left: 21px; right: 0; justify-content: center;
    color: #eef0f3; font-size: 33px; font-weight: 600; gap: 12px;
  }
  .folder .brand-dot { width: 34px; height: 34px; background: #eef0f3; }

  /* Business cards */
  .card { left: 168px; width: 142px; height: 81px; }
  .card-front { top: 373px; background: var(--brand-blue); }
  .card-front .card-curve { position: absolute; inset: 0; width: 100%; height: 100%; }
  .card-details { position: absolute; left: 9px; top: 14px; color: var(--white); font-size: 3.6px; line-height: 5.4px; }
  .card-name { font-size: 5.2px; font-weight: 700; letter-spacing: 0.2px; }
  .card-role { margin-bottom: 3px; }
  .card-gap { height: 3px; }
  .card-front .brand { position: absolute; right: 9px; top: 44px; font-size: 8.5px; gap: 3px; }
  .card-front .brand-dot { width: 8px; height: 8px; }

  .card-back { top: 476px; }
  .card-back .card-curve { position: absolute; inset: 0; width: 100%; height: 100%; }
  .card-back .brand-dot { position: absolute; left: 14px; top: 16px; width: 48px; height: 48px; }
  .card-back-text {
    position: absolute; right: 2px; top: 40px; transform: translate(50%, -50%) rotate(-90deg);
    transform-origin: center; color: var(--white); text-align: center; white-space: nowrap;
    width: 74px; margin-right: 14px;
  }
  .card-back-name { font-size: 10.5px; font-weight: 700; line-height: 11px; }
  .card-back-phone { font-size: 6px; letter-spacing: 0.8px; line-height: 8px; }

  /* Envelopes */
  .envelope { top: 602px; width: 351px; height: 167px; }
  .envelope-front { left: 47px; }
  .envelope-front .brand { position: absolute; left: 20px; top: 22px; font-size: 9px; gap: 4px; }
  .envelope-front .brand-dot { width: 12px; height: 12px; }
  .return-address { position: absolute; left: 20px; top: 40px; font-size: 4px; line-height: 5.4px; }
  .envelope .wave, .slip .wave { height: 38px; }

  .envelope-back { left: 433px; }
  .envelope-flap { position: absolute; left: 0; top: 0; width: 100%; height: 60px; display: block; }
  .envelope-flap path { fill: var(--brand-blue); }
  .envelope-back .brand { position: absolute; top: 18px; left: 0; width: 100%; justify-content: center; color: var(--white); font-size: 7px; gap: 3px; }
  .envelope-back .brand-dot { width: 8px; height: 8px; background: var(--white); }
  .envelope-web { position: absolute; top: 32px; left: 0; width: 100%; text-align: center; color: var(--white); font-size: 3.8px; }

  /* Compliments slip */
  .slip { left: 814px; top: 602px; width: 351px; height: 167px; }
  .slip .brand { position: absolute; left: 18px; top: 22px; font-size: 9px; gap: 4px; }
  .slip .brand-dot { width: 12px; height: 12px; }
  .slip-address { position: absolute; right: 84px; top: 27px; text-align: right; font-size: 4px; line-height: 5.4px; padding-right: 6px; border-right: 0.6px solid var(--muted); }
  .slip-contacts { position: absolute; left: 275px; top: 26px; font-size: 4px; line-height: 5.6px; list-style: none; }
  .slip-contacts li { display: flex; align-items: center; gap: 3px; }
  .slip-contacts svg { width: 4px; height: 4px; fill: var(--brand-blue); flex: none; }
  .slip-greeting {
    position: absolute; left: 82px; top: 74px; width: 230px; text-align: center;
    font-family: "Pinyon Script", cursive; color: var(--brand-blue); font-size: 32px; line-height: 40px;
  }
</style>
</head>
<body>

  <!-- Letterhead -->
  <section class="piece letterhead" aria-label="Letterhead">
    <div class="brand"><span class="brand-dot"></span>Moxy Fen</div>
    <svg class="wave" viewBox="0 0 100 30" preserveAspectRatio="none" aria-hidden="true">
      <path class="wave-grey" d="M0,0 C22,18 62,23 100,8 L100,30 L0,30 Z"/>
      <path class="wave-blue" d="M0,5 C25,22 65,25 100,12 L100,30 L0,30 Z"/>
    </svg>
    <div class="letterhead-footer">
      <p>PO Box 4410, Ashcombe Vale, VIC 3190, Australia</p>
      <p>P: 1300 669 439&nbsp; C: 61 412 557 218&nbsp; E: dara@moxyfen.example&nbsp; W: www.moxyfen.example</p>
    </div>
  </section>

  <!-- Presentation folder -->
  <section class="piece folder" aria-label="Presentation folder">
    <div class="folder-spine"></div>
    <div class="brand"><span class="brand-dot"></span>Moxy Fen</div>
  </section>

  <!-- Business card front -->
  <section class="piece card card-front" aria-label="Business card front">
    <svg class="card-curve" viewBox="0 0 142 81" preserveAspectRatio="none" aria-hidden="true">
      <path fill="var(--brand-grey)" d="M142,0 L92,0 C70,6 62,30 70,52 C78,70 100,81 142,81 Z"/>
      <path fill="var(--paper)" d="M142,0 L96,0 C78,6 72,28 79,48 C86,66 108,78 142,78 Z"/>
    </svg>
    <div class="card-details">
      <p class="card-name">DARA QUILL</p>
      <p>CEO</p>
      <p class="card-role">Lead Agile Coach</p>
      <p>PO Box 4410</p>
      <p>Ashcombe Vale</p>
      <p>VIC 3190, Australia</p>
      <div class="card-gap"></div>
      <p>+61 412 557 218</p>
      <p>dara@moxyfen.example</p>
      <p>www.moxyfen.example</p>
    </div>
    <div class="brand"><span class="brand-dot"></span>Moxy Fen</div>
  </section>

  <!-- Business card back -->
  <section class="piece card card-back" aria-label="Business card back">
    <svg class="card-curve" viewBox="0 0 142 81" preserveAspectRatio="none" aria-hidden="true">
      <path fill="var(--brand-blue)" d="M142,0 L112,0 C100,18 100,62 112,81 L142,81 Z"/>
    </svg>
    <span class="brand-dot"></span>
    <div class="card-back-text">
      <p class="card-back-name">Moxy Fen</p>
      <p class="card-back-phone">1300 669 439</p>
    </div>
  </section>

  <!-- Envelope front -->
  <section class="piece envelope envelope-front" aria-label="Envelope front">
    <div class="brand"><span class="brand-dot"></span>Moxy Fen</div>
    <div class="return-address">
      <p>PO Box 4410</p>
      <p>Ashcombe Vale</p>
      <p>VIC 3190, Australia</p>
    </div>
    <svg class="wave" viewBox="0 0 100 30" preserveAspectRatio="none" aria-hidden="true">
      <path class="wave-grey" d="M0,0 C22,18 62,23 100,8 L100,30 L0,30 Z"/>
      <path class="wave-blue" d="M0,7 C25,23 65,26 100,12 L100,30 L0,30 Z"/>
    </svg>
  </section>

  <!-- Envelope back -->
  <section class="piece envelope envelope-back" aria-label="Envelope back">
    <svg class="envelope-flap" viewBox="0 0 351 60" preserveAspectRatio="none" aria-hidden="true">
      <path d="M0,0 L351,0 L351,8 L343,52 Q341,60 332,60 L19,60 Q10,60 8,52 L0,8 Z"/>
    </svg>
    <div class="brand"><span class="brand-dot"></span>Moxy Fen</div>
    <p class="envelope-web">www.moxyfen.example</p>
  </section>

  <!-- Compliments slip -->
  <section class="piece slip" aria-label="Compliments slip">
    <div class="brand"><span class="brand-dot"></span>Moxy Fen</div>
    <div class="slip-address">
      <p>PO Box 4410</p>
      <p>Ashcombe Vale</p>
      <p>VIC 3190, Australia</p>
    </div>
    <ul class="slip-contacts">
      <li><svg viewBox="0 0 10 10"><path d="M2,1 L4,1 L5,3 L4,4 Q5,6 6,6 L7,5 L9,6 L9,8 Q8,9 7,9 Q1,8 1,3 Q1,2 2,1 Z"/></svg>1300 669 439</li>
      <li><svg viewBox="0 0 10 10"><rect x="2.5" y="0.5" width="5" height="9" rx="1"/></svg>61 412 557 218</li>
      <li><svg viewBox="0 0 10 10"><rect x="0.5" y="2" width="9" height="6"/></svg>dara@moxyfen.example</li>
      <li><svg viewBox="0 0 10 10"><circle cx="5" cy="5" r="4.5"/></svg>www.moxyfen.example</li>
    </ul>
    <p class="slip-greeting">With Compliments</p>
    <svg class="wave" viewBox="0 0 100 30" preserveAspectRatio="none" aria-hidden="true">
      <path class="wave-grey" d="M0,0 C22,18 62,23 100,8 L100,30 L0,30 Z"/>
      <path class="wave-blue" d="M0,7 C25,23 65,26 100,12 L100,30 L0,30 Z"/>
    </svg>
  </section>

</body>
</html>
```